Personal website for my flying adventures

It is the website for my personal flying adventures.

1. I flew around the world in 2011 and became the first Chinese citizen ever flying the single engine airplane around the world in the history and also the first ever to land the single engine airplane in Halvern Ridge airport.
2. I am organizing the "Copper Kestrels Aerobatic Flying Team" in China
3. I am sharing my flying experiences regularly
4. I am writing the book about flying around the world.

Visit: www.lutanmo.com and www.tanmoskyloop.com for more information and pictures on my flying activities. Need connect two websites together well.

Target Market(s)

Young pilots

Industry/Entity Type

Airport

Requirements
Must have
• Must have the logo of "Tanmo Sky Loop"
• Must have the logo of "Copper Kestrels"
• Must have my flying pictures

```html
<!DOCTYPE html>
<html lang="en">
<head>
<meta charset="utf-8">
<title>Tanmo Sky Loop</title>
<link href="https://fonts.googleapis.com/css2?family=PT+Sans+Narrow:wght@400;700&family=Source+Sans+3:wght@400;600&display=swap" rel="stylesheet">
<style>
:root{
  --red:#d7262f;
  --blue:#1fa0db;
  --ink:#222;
  --grey:#555;
  --line:#d9d9d9;
  --footer:#4a4a4a;
  --footer-text:#ddd;
  --circle:rgba(110,96,82,.88);
}
*{margin:0;padding:0;box-sizing:border-box}
html,body{width:1200px;height:1171px;overflow:hidden;background:#fff}
body{position:relative;font-family:"Source Sans 3",sans-serif;color:var(--ink)}
.abs{position:absolute}
.narrow{font-family:"PT Sans Narrow",sans-serif}

/* header */
.header{left:0;top:0;width:1200px;height:73px;background:#fff}
.logo-oval{left:183px;top:0;width:180px;height:133px;background:#fff;border-radius:0 0 90px 90px / 0 0 60px 60px;z-index:3;text-align:center}
.logo-mark{display:block;margin:14px auto 6px;width:62px;height:62px;border-radius:50%;background:var(--blue)}
.logo-name{font-family:"PT Sans Narrow",sans-serif;font-weight:700;font-size:15px;color:var(--red);letter-spacing:.5px}
.logo-url{font-size:9px;color:var(--red);font-weight:600;margin-top:2px}
.util{right:180px;top:25px;display:flex;align-items:center;font-size:10px;color:var(--grey)}
.lang{margin-left:6px;width:84px;height:22px;border:1px solid #bbb;border-radius:3px;display:flex;align-items:center;justify-content:space-between;padding:0 8px;background:linear-gradient(#fff,#eee);color:#333}
.util-nav{display:flex;margin-left:26px}
.util-nav span{font-size:9.5px;color:#444}
.util-nav i{font-style:normal;margin:0 22px;color:#777}

/* hero */
.hero{left:0;top:73px;width:1200px;height:502px;background:linear-gradient(180deg,#6b6e74 0%,#c9915a 22%,#e58a3c 38%,#7a5a44 60%,#3c3a3a 100%)}
.main-nav{right:185px;top:94px;display:flex;gap:76px;z-index:2}
.main-nav span{font-family:"PT Sans Narrow",sans-serif;font-size:14.5px;color:#fff}
.hero-circle{left:727px;top:184px;width:288px;height:288px;border-radius:50%;background:var(--circle);text-align:center;color:#eee}
.hero-circle h1{font-family:"PT Sans Narrow",sans-serif;font-weight:700;font-size:64px;line-height:1;margin-top:52px;color:#e8e4de}
.hero-circle h2{font-family:"PT Sans Narrow",sans-serif;font-weight:400;font-size:27px;line-height:1;margin-top:6px;color:#e8e4de}
.hero-circle hr{border:0;border-top:1px solid rgba(255,255,255,.35);width:220px;margin:12px auto 14px}
.hero-circle p{font-size:9px;line-height:19px;width:230px;margin:0 auto;color:#fff}
.dots{left:978px;top:552px;display:flex;gap:4px}
.dots b{width:11px;height:11px;border-radius:50%;background:rgba(255,255,255,.55)}
.dots b:first-child{background:rgba(255,255,255,.85)}

/* sponsors */
.sp-title{left:182px;top:593px;font-size:17px;color:var(--red)}
.sp-tag{left:182px;top:617px;font-size:10.5px;font-weight:600;letter-spacing:-.2px}
.sp-arrows{left:989px;top:614px;display:flex;gap:3px}
.sp-arrows span{width:14px;height:14px;background:#bbb}
.sp-logos{left:182px;top:652px;width:838px;height:46px;display:flex;align-items:center;justify-content:space-between}
.sp-logos span{font-size:15px;font-weight:600;color:#2a66b8;display:flex;align-items:center;gap:6px}
.sp-logos span i{width:12px;height:12px;border-radius:50%;background:currentColor}
.rule-full{left:0;top:716px;width:1200px;height:2px;background:#e6e6e6}

/* columns */
.col{top:748px;width:261px}
.col h3{font-family:"Source Sans 3",sans-serif;font-weight:400;font-size:16.5px;color:#333;margin-left:2px;height:26px}
.col .bar{height:5px;background:var(--blue)}
.col .photo{margin-top:3px;height:108px;position:relative}
.col .btn{position:absolute;left:-5px;top:76px}
.col p{font-size:9px;line-height:15.5px;margin:15px 0 0 2px;color:#222}
.btn{background:var(--red);color:#fff;font-size:9px;font-weight:600;padding:0 13px;height:21px;line-height:21px;display:inline-block}
.rule{left:180px;top:975px;width:840px;height:1px;background:var(--line)}

/* pilot */
.pilot-title{left:180px;top:994px;font-family:"PT Sans Narrow",sans-serif;font-size:26px;font-weight:700;color:#444}
.pilot-btn{left:180px;top:1030px}
.pilot-sep{left:295px;top:999px;width:1px;height:52px;background:var(--line)}
.pilot-text{left:312px;top:1001px;width:706px;font-size:9px;line-height:15.5px}

/* footer */
.footer{left:0;top:1083px;width:1200px;height:88px;background:repeating-linear-gradient(45deg,#4d4d4d 0 2px,#474747 2px 4px)}
.pdf-badge{left:185px;top:1094px;width:64px;height:64px;border-radius:50%;background:radial-gradient(circle at 40% 35%,#f2545b,#c8141d 70%)}
.fi-title{left:261px;top:1100px;font-family:"PT Sans Narrow",sans-serif;font-size:22px;color:#c9c9c9}
.fi-sub{left:261px;top:1128px;font-family:"PT Sans Narrow",sans-serif;font-size:13px;color:#c9c9c9}
.f-sep{left:469px;top:1095px;width:1px;height:60px;background:#666}
.f-nav{left:488px;top:1111px;display:flex;font-size:8px;color:var(--footer-text)}
.f-nav i{font-style:normal;margin:0 10px}
.f-copy{left:488px;top:1128px;font-size:7.5px;color:var(--footer-text)}
.social{left:945px;top:1114px;display:flex;gap:5px}
.social span{width:22px;height:22px;border-radius:4px;background:linear-gradient(#c8c8c8,#8e8e8e)}
</style>
</head>
<body>

<header class="abs header"></header>
<div class="abs logo-oval">
  <span class="logo-mark"></span>
  <div class="logo-name">TANMO SKY LOOP</div>
  <div class="logo-url">WWW.LUTANMO.COM</div>
</div>
<div class="abs util">
  Select Language :
  <div class="lang"><span>English</span><span>&#9662;</span></div>
  <nav class="util-nav"><span>HOME</span><i>|</i><span>CONTESTS</span><i>|</i><span>STORE</span></nav>
</div>

<section class="abs hero" role="img" aria-label="Business jet parked on a wet runway at sunset"></section>
<nav class="abs main-nav"><span>THE EXPEDITION</span><span>MEDIA ROOM</span><span>SPONSORS</span><span>TANMO TRACKER</span></nav>
<div class="abs hero-circle">
  <h1>TANMO</h1>
  <h2>SKY LOOP</h2>
  <hr>
  <p>WELCOME TO THE ONLINE MEDIA ROOM FOR THE TANMO SKY LOOP WHERE YOU CAN FIND PRESS RELEASES AND OTHER NEWS</p>
</div>
<div class="abs dots"><b></b><b></b><b></b></div>

<h2 class="abs sp-title">SPONCERS</h2>
<p class="abs sp-tag">GLOBAL SPONSORSHIP OPPORTUNITIES AVAILABLE INTENDED TO TOUCH THE HEARTS AND MINDS OF OVER 1.3 BILLION CHINESE.</p>
<div class="abs sp-arrows"><span></span><span></span></div>
<div class="abs sp-logos">
  <span><i></i>Lantern Hub</span>
  <span style="color:#d7262f">Civic Daily</span>
  <span style="color:#1e8fc4">Lantern Micro</span>
  <span style="color:#1a3f8f">RIVET Airframe Parts</span>
  <span style="color:#333">The Harrowgate</span>
  <span style="color:#2d5f9a">Delta Valley Chamber</span>
</div>
<div class="abs rule-full"></div>

<article class="abs col" style="left:180px">
  <h3>ABOUT TANMO SKY LOOP</h3>
  <div class="bar"></div>
  <div class="photo" role="img" aria-label="Pilot in uniform beside a red propeller aircraft" style="background:linear-gradient(180deg,#9aa2ad,#c9c4bd 55%,#7d7a76)"><span class="btn">READ MORE</span></div>
  <p>Welcome to the Online Media Room for the Tanmo Sky Loop where you can find press releases and other news:<br>Ash blocks Tanmo's way: Memphis aviator stuck in Canada</p>
</article>
<article class="abs col" style="left:469px">
  <h3>MEDIA ROOM</h3>
  <div class="bar"></div>
  <div class="photo" role="img" aria-label="Close-up of a red jet engine under an aircraft wing" style="background:linear-gradient(135deg,#b9c6d3,#e6edf3 45%,#d8333a 65%,#8e1b20)"><span class="btn">READ MORE</span></div>
  <p>Welcome to the Online Media Room for the Tanmo Sky Loop where you can find press releases and other news:<br>Ash blocks Tanmo's way: Memphis aviator stuck in Canada</p>
</article>
<article class="abs col" style="left:758px">
  <h3>THE EXPEDITION</h3>
  <div class="bar"></div>
  <div class="photo" role="img" aria-label="Business jet flying above clouds and coastline" style="background:linear-gradient(160deg,#6f7c70,#c6cdd0 50%,#52606a)"><span class="btn">READ MORE</span></div>
  <p>Welcome to the Online Media Room for the Tanmo Sky Loop where you can find press releases and other news:<br>Ash blocks Tanmo's way: Memphis aviator stuck in Canada</p>
</article>

<div class="abs rule"></div>
<h2 class="abs pilot-title">THE PILOT</h2>
<span class="abs btn pilot-btn">READ MORE</span>
<div class="abs pilot-sep"></div>
<p class="abs pilot-text">Tanmo Lu was born in Changsha City, Hunan province of People's Republic of China in 1971. After coming to the United States, he earned his MBA from the University of Larkfield in 1998. Tanmo formed Brightvale Supply, Inc., a construction material company in Memphis, in 1999. Tanmo Lu has grown the company from one man operation to 400 employees in less than 10 years. His successful business venture now has two manufacturing facilities in China and four US branch offices.</p>

<footer class="abs footer"></footer>
<div class="abs pdf-badge" role="img" aria-label="Download badge"></div>
<div class="abs fi-title">FLIGHT ITINERARY</div>
<div class="abs fi-sub">DOWNLOAD LATEST FLIGHT ITINERARY</div>
<div class="abs f-sep"></div>
<nav class="abs f-nav"><span>HOME</span><i>|</i><span>THE EXPEDITION</span><i>|</i><span>MEDIA ROOM</span><i>|</i><span>SPONSORS</span><i>|</i><span>TANMO TRACKER</span><i>|</i><span>CONTESTS</span><i>|</i><span>STORE</span></nav>
<div class="abs f-copy">COPYRIGHT © 2013 TANMO SKY LOOP. ALL RIGHTS RESERVED.</div>
<div class="abs social"><span aria-label="Social link"></span><span aria-label="Social link"></span><span aria-label="Social link"></span></div>

</body>
</html>
```